Business Card Design (NEW FILES)

ATTENTION: New vector files are available. Please update your design to reflect/use the new (better resolution) logo images.

Seeking a unique and professional business card design for a commercial drone photography/videography business. The layout should feature
the logo (attached) and include the following information:
Owen Tarrick
614-502-7738
www.skylarkreelworks.example
NRD Certified Remote Pilot

Owen Tarrick

```html
<!DOCTYPE html>
<html lang="en">
<head>
<meta charset="utf-8">
<title>Skylark Reelworks – Business Card</title>
<link href="https://fonts.googleapis.com/css2?family=Montserrat:wght@400;500;700;800&display=swap" rel="stylesheet">
<style>
  :root {
    --stage: #2b2b2b;
    --navy: #1e1f45;
    --ink: #1e1f45;
    --paper: #ffffff;
    --copper: #e2814a;
    --text: #2a2a2a;
    --muted: #4a4a4a;
  }
  * { box-sizing: border-box; margin: 0; padding: 0; }
  html, body { width: 1200px; height: 688px; overflow: hidden; }
  body {
    background: var(--stage);
    font-family: "Montserrat", sans-serif;
    position: relative;
  }
  .card {
    position: absolute;
    top: 195px;
    width: 525px;
    height: 300px;
    border-radius: 3px;
    box-shadow: 0 14px 30px rgba(0,0,0,.45);
  }
  .card--front { left: 45px; background: var(--navy); }
  .card--back  { left: 630px; background: var(--paper); }

  .brand {
    position: absolute;
    display: flex;
    align-items: center;
    gap: 12px;
    font-weight: 500;
    letter-spacing: .04em;
    text-transform: uppercase;
  }
  .brand__dot { border-radius: 50%; flex: none; }
  .card--front .brand {
    left: 50%; top: 50%;
    transform: translate(-50%, -50%);
    color: var(--paper);
    font-size: 30px;
  }
  .card--front .brand__dot { width: 22px; height: 22px; background: var(--copper); }

  .card--back .brand {
    left: 26px; top: 142px;
    color: var(--ink);
    font-size: 17px;
    gap: 8px;
  }
  .card--back .brand__dot { width: 13px; height: 13px; background: var(--copper); }

  .divider {
    position: absolute;
    left: 276px; top: 60px;
    width: 2px; height: 180px;
    background: var(--copper);
  }
  .details { position: absolute; left: 298px; top: 62px; }
  .details__name { font-size: 21px; font-weight: 800; color: var(--ink); }
  .details__role { font-size: 12px; color: var(--muted); margin-top: 2px; }
  .details__creds {
    margin-top: 14px;
    font-size: 12.5px; font-weight: 700;
    color: var(--copper); line-height: 1.3;
  }
  .contact { list-style: none; margin-top: 14px; }
  .contact__item {
    display: flex; align-items: center; gap: 9px;
    font-size: 11.5px; color: var(--text);
    line-height: 1.75;
  }
  .contact__icon { width: 11px; height: 11px; fill: var(--ink); flex: none; }
</style>
</head>
<body>
  <section class="card card--front" aria-label="Card front">
    <div class="brand"><span class="brand__dot"></span>Skylark Reelworks</div>
  </section>

  <section class="card card--back" aria-label="Card back">
    <div class="brand"><span class="brand__dot"></span>Skylark Reelworks</div>
    <div class="divider"></div>
    <div class="details">
      <h1 class="details__name">Owen Tarrick</h1>
      <p class="details__role">Owner</p>
      <p class="details__creds">NRD Certified Remote Pilot<br>Fully Insured</p>
      <ul class="contact">
        <li class="contact__item">
          <svg class="contact__icon" viewBox="0 0 24 24"><path d="M6.6 10.8a15.1 15.1 0 0 0 6.6 6.6l2.2-2.2c.3-.3.7-.4 1-.2 1.1.4 2.3.6 3.6.6.6 0 1 .4 1 1V20c0 .6-.4 1-1 1A17 17 0 0 1 3 4c0-.6.4-1 1-1h3.5c.6 0 1 .4 1 1 0 1.3.2 2.5.6 3.6.1.3 0 .7-.2 1z"/></svg>
          614-502-7738
        </li>
        <li class="contact__item">
          <svg class="contact__icon" viewBox="0 0 24 24"><path d="M2 5h20v14H2zm2 2v.5l8 5 8-5V7zm0 2.9V17h16V9.9l-8 5z"/></svg>
          info@skylarkreelworks.example
        </li>
        <li class="contact__item">
          <svg class="contact__icon" viewBox="0 0 24 24"><circle cx="12" cy="12" r="10"/><path d="M2 12h20M12 2c3 3 3 17 0 20M12 2c-3 3-3 17 0 20" stroke="#fff" stroke-width="1.5" fill="none"/></svg>
          www.skylarkreelworks.example
        </li>
      </ul>
    </div>
  </section>
</body>
</html>
```